Dietitian/Nutritionist seeks trifold marketing brochure

We need a trifold brochure for marketing to patients within a doctors surgery. This will be a source of information for prospective patients, what they can expect and how to contact us. The brochure needs to have some key information such as a brief description of the services available, fees, locations of clinics and contact information. Our current brochure has been uploaded which has the information you need to complete this project. The files you provide will allow us to edit the information at a later date as pricing and services change.

Target Market(s)

Patients who have been referred to see a dietitian/nutritionist and people who are considering seeing a dietitian/nutritionist but haven't decided

Industry/Entity Type

Dietician

Font styles to use
Serif

Colors

Designer to choose colors to be used in the design.

Requirements
Must have
• My logo
• Accredited practising dietitian logo
• My website address and contact details
• Most of the information that is in my current brochure
• Locations/names of the four clinics
Nice to have
• Images that promote cooking, health and wellbeing

```html
<!DOCTYPE html>
<html lang="en">
<head>
<meta charset="utf-8">
<title>Riverbend Nutrition &amp; Dietetics – Trifold Brochure</title>
<link href="https://fonts.googleapis.com/css2?family=Open+Sans:wght@400;600;700&display=swap" rel="stylesheet">
<style>
  :root{
    --navy:#1b2f8f;
    --navy-dark:#14206b;
    --green:#5cb82e;
    --green-dark:#3f9a1c;
    --ink:#1d1d1f;
    --paper:#ffffff;
    --blush:#fbe9e2;
    --cream:#fdf6e8;
    --backdrop:#e9ebee;
  }
  *{box-sizing:border-box;margin:0;padding:0}
  html,body{width:1200px;height:800px;overflow:hidden;background:var(--backdrop)}
  body{font-family:"Open Sans",Arial,sans-serif;color:var(--ink)}
  .brochure{
    position:relative;width:1200px;height:800px;overflow:hidden;
    background:linear-gradient(160deg,var(--blush) 0%,var(--cream) 35%,#fdf1ee 60%,var(--paper) 85%);
  }
  .fold{position:absolute;top:0;bottom:0;width:1px;background:rgba(0,0,0,.06)}
  .fold--one{left:400px}.fold--two{left:800px}
  .panel{position:absolute;top:0;width:400px;padding:50px 38px 0}
  .panel--about{left:0}
  .panel--visits{left:400px}
  .panel--fees{left:800px;padding-top:0}
  .body-text{font-size:15px;line-height:1.55;text-align:justify}
  .lead{color:var(--navy);font-weight:700}
  .sign-art{
    position:absolute;left:70px;top:360px;width:230px;height:120px;border-radius:18px;
    background:linear-gradient(180deg,#3f63c9,#1b2f8f);box-shadow:0 6px 14px rgba(0,0,0,.25);
  }
  .locations{margin-top:34px}
  .locations__title{display:flex;align-items:center;gap:8px;color:var(--green);font-weight:600;font-size:18px;
    border:1px solid #c9cbd4;padding:2px 10px;width:max-content;background:rgba(255,255,255,.6)}
  .locations__list{list-style:none;margin-top:14px;font-size:15.5px;line-height:1.5}
  .clinic{color:var(--navy);font-weight:600}
  .fees__tab{display:inline-block;background:var(--green);color:#fff;font-weight:600;font-size:18px;
    padding:10px 28px 8px;margin-bottom:14px;letter-spacing:.5px}
  .fees h3{color:var(--navy);font-size:14px;font-weight:700}
  .fees p{font-size:12px;line-height:1.45;color:#333}
  .fees .highlight{color:var(--navy);font-weight:700;font-size:14px}
  .fees .note{color:var(--navy);font-weight:700;font-size:13px;margin-top:8px}
  .fees .price{color:var(--navy);font-weight:700;font-size:15px;line-height:1.4}
  .fees .fund{margin-top:8px}
  .brand{position:absolute;left:845px;top:392px;display:flex;align-items:center;gap:12px}
  .brand__dot{width:40px;height:40px;border-radius:50%;background:var(--navy)}
  .brand__name{color:var(--navy);font-size:24px;font-weight:600;line-height:1.05}
  .produce-art{position:absolute;left:430px;top:440px;width:740px;height:230px;
    background:radial-gradient(ellipse at 30% 55%,#f7a21b 0%,#f6c04a 25%,transparent 55%),
               radial-gradient(ellipse at 62% 50%,#e8432e 0%,#f27a4a 28%,transparent 55%),
               radial-gradient(ellipse at 85% 40%,#5aa52c 0%,#9bcf5a 25%,transparent 55%),
               linear-gradient(90deg,#fde9cf,#fbd7c6);
    border-radius:40px 40px 0 0}
  .wave{position:absolute;left:0;top:0}
  .photo-ring{position:absolute;border-radius:50%;background:#fff;border:10px solid var(--navy)}
  .photo-ring--berries{left:88px;top:548px;width:230px;height:230px}
  .photo-ring--apples{left:1032px;top:485px;width:150px;height:150px;border-width:7px}
  .photo-ring__fill{position:absolute;inset:10px;border-radius:50%}
  .photo-ring--berries .photo-ring__fill{background:radial-gradient(circle at 45% 50%,#d8262a,#7a1430 55%,#e6c79a 85%)}
  .photo-ring--apples .photo-ring__fill{inset:8px;background:radial-gradient(circle at 40% 55%,#9ad13b,#6aa420 45%,#d7282d 75%,#fff 95%)}
  .web{position:absolute;left:470px;top:740px;display:flex;align-items:center;gap:10px;color:#fff;font-size:18px;letter-spacing:.3px}
</style>
</head>
<body>
<main class="brochure">
  <div class="fold fold--one"></div>
  <div class="fold fold--two"></div>

  <section class="panel panel--about">
    <p class="body-text"><span class="lead">Accredited Practising Dietitians (APDs)</span> are university trained experts in food and nutrition, they are able to translate the latest scientific evidence into sensible and practical advice. Dietitians differ from nutritionists as they have specific training in clinical environments such as hospitals. This training allows a dietitian to interpret blood tests, understand any food and medication interactions, and communicate with other health professionals involved in your care.</p>
  </section>
  <div class="sign-art" role="img" aria-label="Blue hanging sign graphic reading Good Health"></div>

  <section class="panel panel--visits">
    <p class="body-text">Seeing a dietitian for the first time involves working with you to develop strategies and goals to improve your health. Follow up visits are recommended to monitor your progress and may include more measurements and new strategies to help YOU realise your goals. Every person is unique and I can</p>
    <div class="locations">
      <h2 class="locations__title">
        <svg width="14" height="18" viewBox="0 0 14 18" aria-hidden="true"><path d="M7 1a6 6 0 0 0-6 6c0 4.5 6 10 6 10s6-5.5 6-10a6 6 0 0 0-6-6z" fill="none" stroke="#1b2f8f" stroke-width="1.6"/><circle cx="7" cy="7" r="2.2" fill="#1b2f8f"/></svg>
        Locations
      </h2>
      <ul class="locations__list">
        <li><span class="clinic">Hillcrest Medical Centre</span><br>Greenfield - Fridays</li>
        <li><span class="clinic">Oakfield Medical</span> - Wednesdays</li>
        <li><span class="clinic">Valley Health</span> Lakeside - Thursdays</li>
        <li><span class="clinic">Northvale Doctors Surgery</span> -<br>Approximately every 4 weeks</li>
      </ul>
    </div>
  </section>

  <section class="panel panel--fees fees">
    <div class="fees__tab">FEES</div>
    <h3>Chronic Disease Management Plans</h3>
    <p>If your Doctor has referred you with a Chronic Disease Management Plan to assist in the ongoing management of your health condition you are eligible for a rebate of <span class="highlight">$52.95 from Medicare.</span></p>
    <p class="note">All Fees are payable on the day Private Patients</p>
    <p class="price">Initial Consultation (60mins) $120<br>Follow up Consultation (30mins) $65</p>
    <h3 class="fund">Private Health Funds</h3>
    <p>Rebates are available through most private health funds but rates vary depending on your level of cover. Check with your fund directly to find out more. Payment is required on the day of your consultation.</p>
  </section>

  <div class="brand">
    <span class="brand__dot"></span>
    <span class="brand__name">Riverbend<br>Nutrition &amp; Dietetics</span>
  </div>

  <div class="produce-art" role="img" aria-label="Photo of fresh fruit, vegetables and glasses of juice"></div>

  <svg class="wave" width="1200" height="800" viewBox="0 0 1200 800" aria-hidden="true">
    <path d="M0 590 C300 560 520 700 800 650 C960 620 1080 560 1200 520 L1200 800 L0 800Z" fill="#1b2f8f"/>
    <path d="M0 606 C300 578 520 716 800 666 C960 638 1080 578 1200 538 L1200 800 L0 800Z" fill="#fff"/>
    <path d="M0 616 C300 590 520 728 800 678 C960 650 1080 590 1200 550 L1200 800 L0 800Z" fill="#5cb82e"/>
  </svg>

  <div class="photo-ring photo-ring--berries"><div class="photo-ring__fill" role="img" aria-label="Photo of a basket of strawberries and mixed berries"></div></div>
  <div class="photo-ring photo-ring--apples"><div class="photo-ring__fill" role="img" aria-label="Photo of green and red apples"></div></div>

  <div class="web">
    <svg width="18" height="18" viewBox="0 0 18 18" aria-hidden="true"><g fill="none" stroke="#fff" stroke-width="1.4"><circle cx="9" cy="9" r="7.5"/><ellipse cx="9" cy="9" rx="3.3" ry="7.5"/><path d="M1.5 9h15M3 5h12M3 13h12"/></g></svg>
    www.riverbenddietitian.com.au
  </div>
</main>
</body>
</html>
```